Maple Grove Schools | brand new stationery!

We need stationery design with our new logo! Our company updated it's name and image and we like to incorporate the new one on our stationery, business cards and email signature. We are looking for fresh, new ideas!
Industry: Childcare, Elementary and Middle School
Company Name: Maple Grove Schools
Tagline: Bright Futures Start Here
Main colors: Blue, white and a little yellow
Star shape is something new for us! Do you see a way to incorporate it as a design element?

```html
<!DOCTYPE html>
<html lang="en">
<head>
<meta charset="utf-8">
<title>Maple Grove Schools – Stationery</title>
<link href="https://fonts.googleapis.com/css2?family=Poppins:wght@400;500;600&family=Noto+Serif:wght@400&display=swap" rel="stylesheet">
<style>
  :root{
    --navy:#041c6f;
    --ink:#1c1c1c;
    --paper:#ffffff;
    --backdrop:#d9d9d9;
    --rule:#2a2a2a;
    --faint:#ececec;
  }
  *{box-sizing:border-box;margin:0;padding:0}
  html,body{width:1200px;height:749px;overflow:hidden;background:var(--backdrop)}
  .canvas{position:relative;width:1200px;height:749px}
  .sheet{position:absolute;background:var(--paper);box-shadow:1px 1px 0 #555}
  .brand{position:absolute;display:flex;align-items:center;gap:5px;font-family:"Poppins",sans-serif;font-weight:500;color:var(--ink);white-space:nowrap}
  .brand-dot{border-radius:50%;background:var(--navy);flex:none}
  .watermark{position:absolute;border-radius:50%;background:var(--faint)}
  .rule{position:absolute;height:1px;background:var(--rule)}
  .contact{position:absolute;display:flex;align-items:center;gap:4px;font-family:"Noto Serif",serif;color:var(--ink);line-height:1.25;white-space:nowrap}
  .icon{flex:none;background:var(--navy);display:flex;align-items:center;justify-content:center}
  .icon svg{width:70%;height:70%;fill:none;stroke:#fff;stroke-width:2}

  /* letterhead */
  .letterhead{left:388px;top:133px;width:370px;height:479px}
  .letterhead .brand{left:96px;top:12px;font-size:16px}
  .letterhead .brand-dot{width:20px;height:20px}
  .letterhead .watermark{left:115px;top:160px;width:120px;height:120px}
  .letterhead .rule{left:27px;top:444px;width:320px}
  .letterhead .contact{font-size:8px;top:453px;gap:5px}
  .letterhead .icon{width:16px;height:16px}

  /* business card */
  .card{left:161px;top:335px;width:347px;height:105px}
  .card .name{position:absolute;left:18px;top:16px;font-family:"Poppins",sans-serif;font-weight:500;font-size:9px;color:var(--navy)}
  .card .title{position:absolute;left:18px;top:28px;font-family:"Noto Serif",serif;font-size:7px;color:var(--ink)}
  .card .contact{font-size:6.8px}
  .card .icon{width:10px;height:10px}
  .card .rule{left:18px;top:72px;width:228px}
  .card .brand{left:250px;top:21px;width:76px;flex-direction:column;gap:4px;font-size:11.5px;text-align:center;line-height:1.1}
  .card .brand-dot{width:22px;height:22px}

  /* envelope */
  .env-front{left:799px;top:231px;width:295px;height:147px}
  .env-front .brand{left:14px;top:8px;font-size:11px}
  .env-front .brand-dot{width:16px;height:16px}
  .env-front .watermark{left:200px;top:34px;width:72px;height:72px}
  .env-front .rule{left:14px;top:116px;width:254px}
  .env-front .contact{font-size:6px;top:123px}
  .env-front .icon{width:12px;height:12px}
  .env-back{left:799px;top:387px;width:295px;height:148px}
  .env-back .flap{position:absolute;left:0;top:0;width:295px;height:36px}
  .env-back .watermark{left:205px;top:70px;width:68px;height:68px}
</style>
</head>
<body>
<div class="canvas">

  <section class="sheet letterhead" aria-label="Letterhead">
    <div class="brand"><span class="brand-dot"></span>Maple Grove Schools</div>
    <div class="watermark" role="img" aria-label="Faint brand star decoration"></div>
    <div class="rule"></div>
    <div class="contact" style="left:27px">
      <span class="icon"><svg viewBox="0 0 24 24"><path d="M6 3l4 4-2 3a11 11 0 006 6l3-2 4 4-3 3C10 21 3 14 3 6z"/></svg></span>
      <span>044-555 210 340<br>044-555 210 341</span>
    </div>
    <div class="contact" style="left:115px">
      <span class="icon"><svg viewBox="0 0 24 24"><circle cx="12" cy="12" r="9"/><path d="M3 12h18M12 3c4 4 4 14 0 18M12 3c-4 4-4 14 0 18"/></svg></span>
      <span>info@maplegrove.org<br>www.maplegrove.org</span>
    </div>
    <div class="contact" style="left:234px">
      <span class="icon"><svg viewBox="0 0 24 24"><path d="M12 21s-6-7-6-11a6 6 0 0112 0c0 4-6 11-6 11z"/><circle cx="12" cy="10" r="2"/></svg></span>
      <span>Your Address line here<br>Country Code 0123456</span>
    </div>
  </section>

  <section class="sheet card" aria-label="Business card">
    <div class="name">Elena Marsh</div>
    <div class="title">Managing Director</div>
    <div class="contact" style="left:18px;top:45px">
      <span class="icon"><svg viewBox="0 0 24 24"><path d="M6 3l4 4-2 3a11 11 0 006 6l3-2 4 4-3 3C10 21 3 14 3 6z"/></svg></span>
      <span>044-555 210 340<br>044-555 210 341</span>
    </div>
    <div class="contact" style="left:92px;top:45px">
      <span class="icon"><svg viewBox="0 0 24 24"><rect x="3" y="6" width="18" height="12"/><path d="M3 6l9 7 9-7"/></svg></span>
      <span>info@maplegrove.org<br>www.maplegrove.org</span>
    </div>
    <div class="rule"></div>
    <div class="contact" style="left:18px;top:78px">
      <span class="icon"><svg viewBox="0 0 24 24"><path d="M12 21s-6-7-6-11a6 6 0 0112 0c0 4-6 11-6 11z"/><circle cx="12" cy="10" r="2"/></svg></span>
      <span>Your Address line here, Country Code 0123456</span>
    </div>
    <div class="brand"><span class="brand-dot"></span><span>Maple Grove<br>Schools</span></div>
  </section>

  <section class="sheet env-front" aria-label="Envelope front">
    <div class="brand"><span class="brand-dot"></span>Maple Grove Schools</div>
    <div class="watermark" role="img" aria-label="Faint brand star decoration"></div>
    <div class="rule"></div>
    <div class="contact" style="left:14px">
      <span class="icon"><svg viewBox="0 0 24 24"><path d="M6 3l4 4-2 3a11 11 0 006 6l3-2 4 4-3 3C10 21 3 14 3 6z"/></svg></span>
      <span>044-555 210 340<br>044-555 210 341</span>
    </div>
    <div class="contact" style="left:85px">
      <span class="icon"><svg viewBox="0 0 24 24"><circle cx="12" cy="12" r="9"/><path d="M3 12h18M12 3c4 4 4 14 0 18M12 3c-4 4-4 14 0 18"/></svg></span>
      <span>info@maplegrove.org<br>www.maplegrove.org</span>
    </div>
    <div class="contact" style="left:179px">
      <span class="icon"><svg viewBox="0 0 24 24"><path d="M12 21s-6-7-6-11a6 6 0 0112 0c0 4-6 11-6 11z"/><circle cx="12" cy="10" r="2"/></svg></span>
      <span>Your Address line here<br>Country Code 0123456</span>
    </div>
  </section>

  <section class="sheet env-back" aria-label="Envelope back">
    <svg class="flap" viewBox="0 0 295 36" preserveAspectRatio="none"><polygon points="0,0 295,0 284,36 12,36" fill="var(--navy)"/></svg>
    <div class="watermark" role="img" aria-label="Faint brand star decoration"></div>
  </section>

</div>
</body>
</html>
```